Field Basket - Store need a label design

We need a Label Design for our Cosmetic Line with Hemp Cosmetics. We do not want a hemp leaf on our design. We want our LOGO infront of the design with the name of the product (shower gel, body lotion, .....) The ingredients must be included as well as in the bottle within 12 months. The font is smaller than 3mm. Generally, the font must be at least 2mm in size. What we need: 100x140mm 200ml E 12m 4x as: Hemp - shampoo, shower gel, body lotion and hair balm 20x66 mm 50g E (2 pieces for front and back) as: face cream, hand cream 42x52mm as: lip balm (sample how it should look in the uploaded files with the name morvil) What else should be on it: WITHOUT artificial colors and fragrances WITHOUT paraffins WITHOUT silicones with pure hemp seed oil Product not tested on animals Manufacturer: MORVIL A-4812 GRUNDLACH Description: HANF-SHAMPOO 200 ml Skin-mild washing-active ingredients develop a particularly pleasant and gentle cleansing effect. High-quality hemp seed oil nourishes the hair in a natural way and makes it pleasantly soft, loose and supple. BRISK MEADOW- is suitable for all hair types, especially for damaged and dull hair. HEMP SHOWER BATH 200 ml The pleasant foam cleans mildly and gently. The excellent care effect of natural hemp seed oil makes skin and hair pleasantly soft and supple.BRISK MEADOW- is suitable for mild cleansing and care, especially of sensitive skin and damaged hair. HEMP-FOAM BATH 200 ml Skin-mild washing-active ingredients develop a particularly mild and creamy foam. The excellent care effect of natural hemp seed oil makes the skin exceptionally soft and supple.BRISK MEADOW- is suitable for mild cleansing and care, especially of sensitive, rough and chapped skin. HEMP HAIR BALM 200 ml A special combination of natural hemp seed oil and other high-quality vegetable oils cares for the hair perfectly and makes it pleasantly soft, loose, supple, naturally shiny, extremely easy to style and effectively prevents the cleavage of the tips. BRISK MEADOW HEMP HAIR BALM is suitable for all hair types, especially for damaged, damaged, brittle and dull hair, as well as split hair tips. HEMP BODY LOTION 200 ml Pure Hemp Seed Oil nourishes the skin naturally, prevents it from drying out too much and makes it particularly soft and supple.BRISK MEADOW HEMP BODY LOTION is for pleasant body care, especially after bathing, especially in dry, brittle and sensitive skin HEMP FACE CREAM 50 g The particularly high content of pure hemp seed oil nourishes the skin perfectly and makes it unusually soft and supple.BRISK MEADOW HEMP FACE CREAM is suitable for pleasant and moisturizing care of the entire face, especially for dry and brittle skin Skin. HEMP HAND CREAM 50 g The high content of pure hemp seed oil and natural beeswax protects and nourishes the skin perfectly and makes it soft and supple. BRISK MEADOW HEMP HAND CREAM is suitable for protective care especially of stressed, sensitive and brittle skin. HEMP LIP BALM 6 g Natural hemp seed oil, pure beeswax and other valuable ingredients provide long-lasting care for the lips and protect them from adverse weather conditions and dehydration.BRISK MEADOW HEMP LIP BALM is particularly suitable for the lasting care of sensitive, brittle and torn lips. HANF-SHAMPOO Ingredients (INCI): Aqua, Sodium Laureth Sulfate, TEA-Lauryl Sulfate, Disodium Laureth Sulfosuccinate, Potassium Cocoyl Hydrolized Collagen, Linoleamide-DEA, Cannabis Sativa Seed Oil, Natural Perfume, Sodium Chloride, Citric Acid, Potassium Sorbate, Panthenol , Tocopherol, chlorophyll, citral *, citronellol *, geraniol *, limonene *, linalool *. (* natural ingredients of essential oils). HEMP-DUSCHBAD Ingredients (INCI): Aqua, Sodium Laureth Sulfate, TEA-Lauryl Sulfate, Disodium Laureth Sulfosuccinate, Potassium Cocoyl Hydrolized Collagen, Cocoamphodiacetate, Linoleamide-DEA, Cocamidopropylamine Oxide, Cannabis Sativa Seed Oil, Natural Perfume, Coco-Glucoside, Glyceryl Oleate, Sodium Chloride, Citric Acid, Potassium Sorbate, Panthenol, Tocopherol, Chlorophyll, Citral *, Citronellol *, Geraniol *, Limonene *, Linalool *. (* natural ingredients of essential oils). HANF-SCHAUMBAD Ingredients (INCI): Aqua, MIPA-Pareth-25-Sulfate, Cocamidopropyl Betaine, Disodium Laureth Sulfosuccinate, Linoleamide-DEA, Cannabis Sativa Seed Oil, Coco-Glucoside, Glyceryl Oleate, Natural Perfume, Panthenol, Potassium Sorbate, Citric Acid, tocopherol, chlorophyll, citral *, citronellol *, geraniol *, limonene *, linalool *. * (* Natural constituents of essential oils). HANF-HAARBALSAM Ingredients (INCI): Aqua, Ceteareth-20, Cetearyl Alcohol, Dicocodimonium Chloride, Glycerine, Cannabis Sativa Seed Oil, Coco-Glucoside, Glyceryl Oleate, Natural Perfume, Potassium Sorbate, Panthenol, Citric Acid, Tocopherol, Chlorophyll, Citral *, Citronellol *, geraniol *, limonene *, linalool *. (* natural ingredients of essential oils). Hemp Facial Ingredients (INCI): Aqua, Cannabis Sativa Seed Oil, Cetearyl Alcohol, Cetearyl Glucoside, Sodium Cetearyl Sulfate, Hexyl Decanol, Glycerine, Natural Perfume, Benzyl Alcohol, Potassium Sorbate, Sodium Benzoate, Tocopherol, Panthenol, Citric Acid, Citral * , Citronellol *, geraniol *, limonene *, linalool *. (* natural ingredients of essential oils). HANF HAND CREAM Ingredients (INCI): Cannabis sativa Seed Oil, Cocos Nucifera Oil, Cera Alba, Tocopherol, Natural Perfume, Citral *, Citronellol *, Geraniol *, Limonene *, Linalool *. (* natural ingredients of essential oils). HEMP BODY LOTION INGREDIENTS (INCI): Aqua, Cannabis Sativa Seed Oil, Cetearyl Alcohol, Ceteareth-12, Cetearyl Glucoside, Glycerol, Hexyldecanol, Natural Perfume, Benzyl Alcohol, Potassium Sorbate, Sodium Benzoate, Tocopherol, Panthenol, Citric Acid, Geraniol , Limonene *, linalool *, citronellol *, citral *, (* natural constituents of essential oils). HEMP LIP BALM Ingredients (INCI): Cannabis sativa Seed Oil, Cocos nucifera Oil, Cera Alba, Natural Perfume, Citral *, Citronellol *, Geraniol *, Limonene *, Linalool *. (* natural ingredients of essential oils).

Colors

Designer to choose colors to be used in the design.

Requirements
Must have
• The Sentence: Natural Spirit - Feel the nature should be in front of the label as our slogan for the Cosmetic Line
Should not have
• Hemp leaf

```html
<!DOCTYPE html>
<html lang="de">
<head>
<meta charset="utf-8">
<title>Brisk Meadow – Hanf-Kosmetik Etiketten</title>
<link href="https://fonts.googleapis.com/css2?family=Bebas+Neue&family=Roboto+Condensed:wght@300;400&family=Rokkitt:wght@700&family=Yesteryear&family=Montserrat:wght@500&display=swap" rel="stylesheet">
<style>
:root{
  --white:#ffffff;
  --schaumbad:#6f4a5f; --schaumbad-2:#553648;
  --duschbad:#527d69; --duschbad-2:#3d6353;
  --haarbalsam:#a891a7; --haarbalsam-2:#8e7690;
  --lotion:#8d7666; --lotion-2:#6f5a4c;
  --shampoo:#4f78b4; --shampoo-2:#3e62a0;
  --hand:#767290; --hand-2:#5f5b7c;
  --face:#86a85f; --face-2:#6c9048;
  --lip:#5c7bb0;
  --box-dark:rgba(40,20,35,.75);
}
*{box-sizing:border-box;margin:0;padding:0}
html,body{width:1082px;height:1200px;overflow:hidden;background:#fff}
body{position:relative;font-family:"Roboto Condensed",sans-serif;color:var(--white)}

.label{position:absolute;overflow:hidden;color:var(--white)}
.label--big{width:476px;height:340px}
.texture{position:absolute;inset:0}
.schaumbad{left:42px;top:36px;background:var(--schaumbad)}
.schaumbad .texture{background:linear-gradient(160deg,transparent 30%,var(--schaumbad-2) 55%,transparent 80%)}
.duschbad{left:567px;top:36px;background:var(--duschbad)}
.duschbad .texture{background:linear-gradient(160deg,transparent 30%,var(--duschbad-2) 55%,transparent 80%)}
.haarbalsam{left:42px;top:417px;background:var(--haarbalsam)}
.haarbalsam .texture{background:linear-gradient(160deg,transparent 25%,var(--haarbalsam-2) 55%,transparent 85%)}
.lotion{left:567px;top:417px;background:var(--lotion)}
.lotion .texture{background:linear-gradient(160deg,transparent 25%,var(--lotion-2) 55%,transparent 85%)}
.shampoo{left:42px;top:792px;background:var(--shampoo)}
.shampoo .texture{background:linear-gradient(160deg,transparent 25%,var(--shampoo-2) 55%,transparent 85%)}

.brand{position:absolute;left:16px;top:14px;width:188px;text-align:center}
.brand-dot{display:block;width:34px;height:34px;border-radius:50%;background:var(--white);margin:0 auto 4px}
.brand-name{font-family:"Montserrat",sans-serif;font-weight:500;font-size:11.5px;letter-spacing:.5px}
.rule{position:absolute;left:16px;width:188px;height:1.5px;background:var(--white)}
.title{position:absolute;left:16px;top:80px;width:200px;font-family:"Bebas Neue",sans-serif;font-size:34px;letter-spacing:.5px;line-height:1}
.slogan{position:absolute;left:16px;top:141px;width:188px;text-align:center;font-family:"Roboto Condensed",sans-serif;font-size:9.5px;letter-spacing:5.5px;font-weight:400}
.claims{position:absolute;left:24px;top:194px;width:200px;list-style:none;font-family:"Rokkitt",serif;font-weight:700;font-size:8.6px}
.claims li{height:20px;line-height:16px;border-bottom:1px solid rgba(255,255,255,.85)}
.claims li:last-child{border-bottom:none}
.tested{position:absolute;left:16px;top:285px;width:93px;height:40px;background:var(--box-dark);font-size:6.8px;letter-spacing:1.2px;padding:9px 8px;line-height:1.7}
.maker{position:absolute;left:119px;top:291px;font-size:6.6px;letter-spacing:1.3px;line-height:2.4}
.copy{position:absolute;left:277px;top:32px;width:190px;font-size:7.8px;line-height:1.45;font-weight:300}
.copy p{margin-bottom:13px}
.copy .pitch{font-family:"Yesteryear",cursive;font-size:9.4px;line-height:1.3;font-weight:400}
.copy .pitch b{font-family:"Rokkitt",serif;font-size:7.6px;letter-spacing:.3px}
.facts{position:absolute;left:267px;top:285px;width:196px;height:43px;border-top:1.5px solid var(--white);display:flex}
.facts > div{flex:1;display:flex;align-items:center;justify-content:center;border-right:1.5px solid var(--white)}
.facts > div:last-child{border-right:none}
.vol{font-family:"Bebas Neue",sans-serif;font-size:21px}
.vol small{font-family:"Roboto Condensed",sans-serif;font-size:12px;font-weight:300}
.estim{font-family:"Roboto Condensed",sans-serif;font-size:24px;font-weight:300}
.foot{position:absolute;left:277px;bottom:6px;font-size:6.6px;letter-spacing:1.3px}

/* small labels */
.label--strip{width:225px;height:69px}
.hand-back{left:566px;top:792px;background:var(--hand)}
.hand-front{left:566px;top:888px;background:var(--hand)}
.face-back{left:566px;top:967px;background:var(--face)}
.face-front{left:566px;top:1061px;background:var(--face)}
.hand-back .texture,.hand-front .texture{background:linear-gradient(150deg,transparent 30%,var(--hand-2) 60%,transparent 90%)}
.face-back .texture,.face-front .texture{background:linear-gradient(150deg,transparent 30%,var(--face-2) 60%,transparent 90%)}
.strip-copy{position:absolute;left:4px;top:4px;width:124px;font-size:4.8px;line-height:1.35;font-weight:300}
.strip-copy .pitch{font-family:"Yesteryear",cursive;font-size:5.6px;margin-top:4px;line-height:1.25}
.strip-copy .pitch b{font-family:"Rokkitt",serif;font-size:4.6px}
.strip-inci{position:absolute;left:136px;top:4px;width:84px;font-size:3.8px;line-height:1.35;font-weight:300;border-left:1px solid rgba(255,255,255,.8);padding-left:4px;height:40px}
.strip-facts{position:absolute;left:136px;top:51px;width:85px;height:14px;border-top:1px solid #fff;display:flex}
.strip-facts div{flex:1;display:flex;align-items:center;justify-content:center;border-right:1px solid #fff;font-size:7px}
.strip-facts div:last-child{border-right:none}
.mini-brand{position:absolute;left:8px;top:6px;width:40px;text-align:center;font-family:"Montserrat",sans-serif;font-weight:500;font-size:4.5px}
.mini-brand .brand-dot{width:11px;height:11px;margin-bottom:1px}
.mini-title{position:absolute;left:8px;top:28px;width:122px;font-family:"Bebas Neue",sans-serif;font-size:20px;line-height:1;border-top:1px solid #fff;border-bottom:1px solid #fff;padding-top:2px}
.mini-slogan{position:absolute;left:20px;top:53px;font-size:5px;letter-spacing:3px}
.mini-claims{position:absolute;left:148px;top:5px;width:74px;list-style:none;font-family:"Rokkitt",serif;font-weight:700;font-size:4px}
.mini-claims li{height:9.5px;line-height:8px;border-bottom:.6px solid rgba(255,255,255,.8)}
.mini-claims li:last-child{border-bottom:none}
.mini-tested{position:absolute;left:148px;top:50px;width:34px;height:13px;background:rgba(20,40,30,.55);font-size:2.8px;letter-spacing:.4px;padding:2px 3px;line-height:1.5}
.mini-maker{position:absolute;left:186px;top:51px;font-size:2.8px;letter-spacing:.4px;line-height:1.6}
.hand-front .mini-tested{background:rgba(30,25,50,.6)}

.lip{left:863px;top:792px;width:177px;height:143px;background:var(--lip)}
.lip .texture{background:linear-gradient(150deg,transparent 30%,#4a67a0 60%,transparent 90%)}
.lip .mini-brand{left:16px;top:8px;width:50px}
.lip-title{position:absolute;left:4px;top:37px;width:78px;font-family:"Bebas Neue",sans-serif;font-size:15px;line-height:1;border-bottom:1px solid #fff;padding-bottom:1px}
.lip-slogan{position:absolute;left:6px;top:56px;font-size:4px;letter-spacing:1.6px}
.lip-claims{position:absolute;left:12px;top:68px;width:70px;list-style:none;font-family:"Rokkitt",serif;font-weight:700;font-size:3.8px}
.lip-claims li{height:8.5px;line-height:7px;border-bottom:.6px solid rgba(255,255,255,.8)}
.lip-claims li:last-child{border-bottom:none}
.lip-maker{position:absolute;left:4px;top:128px;width:78px;height:11px;background:rgba(20,35,70,.6);font-size:3px;letter-spacing:.4px;padding:1.5px 3px;line-height:1.4}
.lip-copy{position:absolute;left:90px;top:5px;width:84px;font-size:3.4px;line-height:1.4;font-weight:300}
.lip-copy .pitch{font-family:"Yesteryear",cursive;font-size:4.4px;margin:4px 0;line-height:1.25}
.lip-copy .pitch b{font-family:"Rokkitt",serif;font-size:3.6px}
.lip .strip-facts{left:92px;top:124px;width:80px}
</style>
</head>
<body>

<!-- jar icon reused -->
<svg width="0" height="0" style="position:absolute" aria-hidden="true">
  <defs>
    <symbol id="jar" viewBox="0 0 40 34">
      <path d="M4 18 H36 V30 Q36 32 34 32 H6 Q4 32 4 30 Z" fill="none" stroke="#fff" stroke-width="1.6"/>
      <path d="M6 16 L30 2" stroke="#fff" stroke-width="1.6"/>
      <path d="M9 18 L33 4" stroke="#fff" stroke-width="1.2"/>
      <text x="20" y="29" font-size="8" fill="#fff" text-anchor="middle" font-family="Roboto Condensed, sans-serif">12m</text>
    </symbol>
  </defs>
</svg>

<!-- Hanf-Schaumbad -->
<section class="label label--big schaumbad">
  <div class="texture" role="img" aria-label="Weiche, rauchige Wellenstruktur in dunklem Violett"></div>
  <div class="brand"><span class="brand-dot"></span><span class="brand-name">BRISK MEADOW</span></div>
  <div class="rule" style="top:71px"></div>
  <h2 class="title">HANF-SCHAUMBAD</h2>
  <div class="rule" style="top:123px"></div>
  <div class="slogan">FEEL THE NATURE</div>
  <div class="rule" style="top:158px"></div>
  <ul class="claims"><li>OHNE künstliche Farb und Geruchstoffe</li><li>OHNE Paraffine</li><li>OHNE Silikone</li><li>mit reinem Hanfsamenöl</li></ul>
  <div class="tested">PRODUKT NICHT<br>AN TIEREN GETESTET</div>
  <div class="maker">HERSTELLER:<br>MORVIL A-4812 GRUNDLACH</div>
  <div class="copy">
    <p>Hautmilde waschaktive Bestandteile entwickeln einen besonders milden und cremigen Schaum. Die hervorragende Pflegewirkung von naturreinem Hanfsamen-Öl macht die Haut außergewöhnlich weich und geschmeidig.</p>
    <p class="pitch"><b>BRISK MEADOW</b> – eignet sich zur milden Reinigung und Pflege, besonders von empfindlicher, rauer und rissiger Haut.</p>
    <p>Ingredients (INCI): Aqua, MIPA-Pareth-25-Sulfate, Cocamidopropyl Betain, Disodium Laureth Sulfosuccinate, Linoleamide-DEA, Cannabis sativa Seed Oil, Coco-Glucoside, Glyceryl Oleate, Natural Perfume, Panthenol, Potassium Sorbate, Citric Acid, Tocopherol, Chlorophyll, Citral*, Citronellol*, Geraniol*, Limonene*, Linalool*. (* natürliche Bestandteile ätherischer Öle).</p>
  </div>
  <div class="facts"><div class="vol">200<small>ml</small></div><div class="estim">e</div><div><svg width="34" height="30"><use href="#jar"/></svg></div></div>
</section>

<!-- Hanf-Duschbad -->
<section class="label label--big duschbad">
  <div class="texture" role="img" aria-label="Weiche, rauchige Wellenstruktur in Salbeigrün"></div>
  <div class="brand"><span class="brand-dot"></span><span class="brand-name">BRISK MEADOW</span></div>
  <div class="rule" style="top:71px"></div>
  <h2 class="title">HANF-DUSCHBAD</h2>
  <div class="rule" style="top:123px"></div>
  <div class="slogan">FEEL THE NATURE</div>
  <div class="rule" style="top:158px"></div>
  <ul class="claims"><li>OHNE künstliche Farb und Geruchstoffe</li><li>OHNE Paraffine</li><li>OHNE Silikone</li><li>mit reinem Hanfsamenöl</li></ul>
  <div class="tested" style="background:rgba(15,50,40,.7)">PRODUKT NICHT<br>AN TIEREN GETESTET</div>
  <div class="maker">HERSTELLER:<br>MORVIL A-4812 GRUNDLACH</div>
  <div class="copy" style="top:28px">
    <p>Der angenehme Schaum reinigt mild und schonend. Die hervorragende Pflegewirkung von naturreinem Hanfsamen-Öl macht Haut und Haar angenehm weich und geschmeidig.</p>
    <p class="pitch"><b>BRISK MEADOW</b> – eignet sich zur milden Reinigung und Pflege, besonders von empfindlicher Haut und strapaziertem Haar.</p>
    <p>Ingredients (INCI): Aqua, Sodium Laureth Sulfate, TEA-Lauryl Sulfate, Disodium Laureth Sulfosuccinate, Potassium Cocoyl Hydrolized Collagen, Cocoamphodiacetate, Linoleamide-DEA, Cocamidopropylamin Oxide, Cannabis Sativa Seed Oil, Natural Perfume, Coco-Glucoside, Glyceryl Oleate, Sodium Chloride, Citric Acid, Potassium Sorbate, Panthenol, Tocopherol, Chlorophyll, Citral*, Citronellol*, Geraniol*, Limonene*, Linalool*. (* natürliche Bestandteile ätherischer Öle).</p>
  </div>
  <div class="facts"><div class="vol">200<small>ml</small></div><div class="estim">e</div><div><svg width="34" height="30"><use href="#jar"/></svg></div></div>
</section>

<!-- Hanf-Haarbalsam -->
<section class="label label--big haarbalsam">
  <div class="texture" role="img" aria-label="Weiche, rauchige Wellenstruktur in Mauve"></div>
  <div class="brand"><span class="brand-dot"></span><span class="brand-name">BRISK MEADOW</span></div>
  <div class="rule" style="top:71px"></div>
  <h2 class="title" style="font-size:32px">HANF-HAARBALSAM</h2>
  <div class="rule" style="top:123px"></div>
  <div class="slogan">FEEL THE NATURE</div>
  <div class="rule" style="top:158px"></div>
  <ul class="claims"><li>OHNE künstliche Farb und Geruchstoffe</li><li>OHNE Paraffine</li><li>OHNE Silikone</li><li>mit reinem Hanfsamenöl</li></ul>
  <div class="tested" style="background:rgba(70,55,75,.8)">PRODUKT NICHT<br>AN TIEREN GETESTET</div>
  <div class="maker">HERSTELLER:<br>MORVIL A-4812 GRUNDLACH</div>
  <div class="copy" style="top:14px;left:281px">
    <p>Eine spezielle Kombination von naturreinem Hanfsamen-Öl und weiteren hochwertigen Pflanzenölen pflegt das Haar hervorragend und macht es angenehm weich, locker, geschmeidig, natürlich glänzend, äusserst leicht frisierbar und verhindert wirksam die Spaltung der Spitzen.</p>
    <p class="pitch"><b>BRISK MEADOW</b> – eignet sich für alle Haartypen, besonders für strapaziertes, geschädigtes, brüchiges und mattes Haar, sowie bei gespaltenen Haarspitzen.</p>
    <p>Ingredients (INCI): Aqua, Ceteareth-20, Cetearyl Alcohol, Dicocodimonium Chloride, Glycerine, Cannabis sativa Seed Oil, Coco-Glucoside, Glyceryl Oleate, Natural Perfume, Potassium Sorbate, Panthenol, Citric Acid, Tocopherol, Chlorophyll, Citral*, Citronellol*, Geraniol*, Limonene*, Linalool*. (* natürliche Bestandteile ätherischer Öle).</p>
  </div>
  <div class="facts"><div class="vol">200<small>ml</small></div><div class="estim">e</div><div><svg width="34" height="30"><use href="#jar"/></svg></div></div>
</section>

<!-- Hanf-Körperlotion -->
<section class="label label--big lotion">
  <div class="texture" role="img" aria-label="Weiche, rauchige Wellenstruktur in Taupe"></div>
  <div class="brand" style="top:20px"><span class="brand-dot"></span><span class="brand-name">BRISK MEADOW</span></div>
  <div class="rule" style="top:80px"></div>
  <h2 class="title" style="top:90px;font-size:29px">HANF-KÖRPERLOTION</h2>
  <div class="rule" style="top:130px"></div>
  <div class="slogan" style="top:146px">FEEL THE NATURE</div>
  <div class="rule" style="top:163px"></div>
  <ul class="claims" style="top:198px"><li>OHNE künstliche Farb und Geruchstoffe</li><li>OHNE Paraffine</li><li>OHNE Silikone</li><li>mit reinem Hanfsamenöl</li></ul>
  <div class="tested" style="top:291px;background:rgba(50,40,32,.75)">PRODUKT NICHT<br>AN TIEREN GETESTET</div>
  <div class="copy" style="top:34px;left:279px">
    <p>Reines Hanfsamen-Öl pflegt die Haut auf natürliche Weise, verhindert zu starkes Austrocknen und macht sie besonders weich und geschmeidig.</p>
    <p class="pitch"><b>BRISK MEADOW</b> – ist zur angenehmen Körperpflege, besonders nach dem Baden, vor allem bei trockener, spröder und empfindlicher Haut</p>
    <p>Aqua, Cannabis sativa Seed Oil, Cetearyl Alcohol, Ceteareth-12, Cetearyl Glucoside, Glycerine, Hexyldecanol, Natural Perfume, Benzyl Alcohol, Potassium Sorbate, Sodium Benzoate, Tocopherol, Panthenol, Citric Acid, Geraniol*, Limonene*, Linalool*, Citronellol*, Citral*. (* natürliche Bestandteile ätherischer Öle).</p>
  </div>
  <div class="maker" style="left:332px;top:255px">HERSTELLER:<br>MORVIL A-4812 GRUNDLACH</div>
  <div class="facts"><div class="vol">200<small>ml</small></div><div class="estim">e</div><div><svg width="34" height="30"><use href="#jar"/></svg></div></div>
</section>

<!-- Hanf-Shampoo -->
<section class="label label--big shampoo">
  <div class="texture" role="img" aria-label="Weiche, rauchige Wellenstruktur in Blau"></div>
  <div class="brand"><span class="brand-dot"></span><span class="brand-name">BRISK MEADOW</span></div>
  <div class="rule" style="top:71px"></div>
  <h2 class="title">HANF - SHAMPOO</h2>
  <div class="rule" style="top:123px"></div>
  <div class="slogan">FEEL THE NATURE</div>
  <div class="rule" style="top:158px"></div>
  <ul class="claims" style="font-family:'Montserrat',sans-serif;font-weight:500;font-size:8.4px"><li>OHNE künstliche Farb und Geruchstoffe</li><li>OHNE Paraffine</li><li>OHNE Silikone</li><li>mit reinem Hanfsamenöl</li></ul>
  <div class="tested" style="top:290px;background:#2c5a9c">PRODUKT NICHT<br>AN TIEREN GETESTET</div>
  <div class="copy" style="left:277px">
    <p>Hautmilde waschaktive Bestandteile entfalten eine besonders angenehme und schonende Reinigungswirkung. Hochwertiges Hanfsamen-Öl pflegt das Haar auf natürliche Weise und macht es angenehm weich, locker und geschmeidig.</p>
    <p class="pitch"><b>BRISK MEADOW</b> – eignet sich für alle Haartypen, besonders für strapaziertes und mattes Haar.</p>
    <p>Ingredients (INCI): Aqua, Sodium Laureth Sulfate, TEA-Lauryl Sulfate, Disodium Laureth Sulfosuccinate, Potassium Cocoyl Hydrolized Collagen, Linoleamide-DEA, Cannabis Sativa Seed Oil, Natural Perfume, Sodium Chloride, Citric Acid, Potassium Sorbate, Panthenol, Tocopherol, Chlorophyll, Citral*, Citronellol*, Geraniol*, Limonene*, Linalool*. (* natürliche Bestandteile ätherischer Öle).</p>
  </div>
  <div class="facts" style="top:274px"><div class="vol">200<small>ml</small></div><div class="estim">e</div><div><svg width="34" height="30"><use href="#jar"/></svg></div></div>
  <div class="foot">HERSTELLER: MORVIL A-4812 GRUNDLACH</div>
</section>

<!-- Hanf-Handcreme Rückseite -->
<section class="label label--strip hand-back">
  <div class="texture" role="img" aria-label="Rauchige Wellenstruktur in Graulila"></div>
  <div class="strip-copy">
    Der hohe Gehalt an reinem Hanfsamenöl und natürlichem Bienenwachs schützt und pflegt die Haut hervorragend und macht sie weich und geschmeidig.
    <div class="pitch"><b>BRISK MEADOW</b> – eignet sich zur schützenden Pflege besonders von strapazierter, empfindlicher und spröder Haut.</div>
  </div>
  <div class="strip-inci">Ingredients (INCI): Cannabis sativa Seed Oil, Cocos Nucifera Oil, Cera Alba, Tocopherol, Natural Perfume, Citral*, Citronellol*, Geraniol*, Limonene*, Linalool*. (* natürliche Bestandteile ätherischer Öle)</div>
  <div class="strip-facts"><div>50 ml</div><div>e</div><div><svg width="12" height="10"><use href="#jar"/></svg></div></div>
</section>

<!-- Hanf-Handcreme Vorderseite -->
<section class="label label--strip hand-front">
  <div class="texture" role="img" aria-label="Rauchige Wellenstruktur in Graulila"></div>
  <div class="mini-brand"><span class="brand-dot"></span>BRISK MEADOW</div>
  <div class="mini-title">HANF-HANDCREME</div>
  <div class="mini-slogan">FEEL THE NATURE</div>
  <ul class="mini-claims"><li>OHNE künstliche Farb und Geruchstoffe</li><li>OHNE Paraffine</li><li>OHNE Silikone</li><li>mit reinem Hanfsamenöl</li></ul>
  <div class="mini-tested">PRODUKT NICHT<br>AN TIEREN GETESTET</div>
  <div class="mini-maker">HERSTELLER:<br>MORVIL A-4812 GRUNDLACH</div>
</section>

<!-- Hanf-Gesichtscreme Rückseite -->
<section class="label label--strip face-back">
  <div class="texture" role="img" aria-label="Rauchige Wellenstruktur in Hellgrün"></div>
  <div class="strip-copy">
    Der besonders hohe Gehalt an reinem Hanfsamen-Öl pflegt die Haut hervorragend und macht sie ungewöhnlich weich und geschmeidig.
    <div class="pitch"><b>BRISK MEADOW</b> – eignet sich zur angenehmen und feuchtigkeitsspendenden Pflege der gesamten Gesichtspartie besonders bei trockener und spröder Haut.</div>
  </div>
  <div class="strip-inci">Ingredients (INCI): Aqua, Cannabis sativa Seed Oil, Cetearyl Alcohol, Cetearyl Glucoside, Sodium Cetearyl Sulfate, Hexyldecanol, Glycerine, Natural Perfume, Benzyl Alcohol, Potassium Sorbate, Sodium Benzoate, Tocopherol, Panthenol, Citric Acid, Citral*, Citronellol*, Geraniol*, Limonene*, Linalool*.</div>
  <div class="strip-facts"><div>50 ml</div><div>e</div><div><svg width="12" height="10"><use href="#jar"/></svg></div></div>
</section>

<!-- Hanf-Gesichtscreme Vorderseite -->
<section class="label label--strip face-front">
  <div class="texture" role="img" aria-label="Rauchige Wellenstruktur in Hellgrün"></div>
  <div class="mini-brand"><span class="brand-dot"></span>BRISK MEADOW</div>
  <div class="mini-title" style="font-size:18px">HANF-GESICHTSCREME</div>
  <div class="mini-slogan">FEEL THE NATURE</div>
  <ul class="mini-claims"><li>OHNE künstliche Farb und Geruchstoffe</li><li>OHNE Paraffine</li><li>OHNE Silikone</li><li>mit reinem Hanfsamenöl</li></ul>
  <div class="mini-tested">PRODUKT NICHT<br>AN TIEREN GETESTET</div>
  <div class="mini-maker">HERSTELLER:<br>MORVIL A-4812 GRUNDLACH</div>
</section>

<!-- Lippenbalsam -->
<section class="label lip">
  <div class="texture" role="img" aria-label="Rauchige Wellenstruktur in Blau"></div>
  <div class="mini-brand"><span class="brand-dot"></span>BRISK MEADOW</div>
  <div class="lip-title">LIPPENBALSAM</div>
  <div class="lip-slogan">FEEL THE NATURE</div>
  <ul class="lip-claims"><li>OHNE künstliche Farb und Geruchstoffe</li><li>OHNE Paraffine</li><li>OHNE Silikone</li><li>mit reinem Hanfsamenöl</li></ul>
  <div class="lip-maker">HERSTELLER:<br>MORVIL A-4812 GRUNDLACH</div>
  <div class="lip-copy">
    Natürliches Hanfsamenöl, reines Bienenwachs und weitere wertvolle Bestandteile pflegen die Lippen nachhaltig und schützen sie vor ungünstigen Witterungseinflüssen und Austrocknung.
    <div class="pitch"><b>BRISK MEADOW</b> – eignet sich besonders zur nachhaltigen Pflege von empfindlichen, spröden und zu Rissen neigenden Lippen.</div>
    Ingredients (INCI): Cannabis sativa Seed Oil, Cocos nucifera Oil, Cera Alba, Natural Perfume, Citral*, Citronellol*, Geraniol*, Limonene*, Linalool*. (* natürliche Bestandteile ätherischer Öle)
  </div>
  <div class="strip-facts"><div>6g</div><div>e</div><div><svg width="12" height="10"><use href="#jar"/></svg></div></div>
</section>

</body>
</html>
```